Business Card Design Project

We are a construction company in Orange County, CA. We need a two sided business card. We would like the back to be our logo with web URL. Front should included Name, title, address, phone, fax and email address.

our address is
627 West Dorrance Blvd, Suite 308
Anaheim, CA 92718

Our logo files are attached.

Construction

```html
<!DOCTYPE html>
<html lang="en">
<head>
<meta charset="utf-8">
<title>Halvern Business Card</title>
<link href="https://fonts.googleapis.com/css2?family=Source+Sans+3:wght@400;700&display=swap" rel="stylesheet">
<style>
  :root {
    --brand-blue: #1a4a7e;
    --paper: #ffffff;
    --backdrop: #e9e6e1;
  }
  * { margin: 0; padding: 0; box-sizing: border-box; }
  html, body { width: 1200px; height: 444px; overflow: hidden; }
  body {
    background: var(--backdrop);
    font-family: "Source Sans 3", sans-serif;
    position: relative;
  }
  .card {
    position: absolute;
    width: 516px;
    height: 294px;
    box-shadow: 0 4px 10px rgba(0,0,0,0.25);
    overflow: hidden;
  }
  .card-front { left: 70px; top: 76px; background: var(--paper); }
  .card-back { left: 614px; top: 74px; background: var(--brand-blue); }

  .wordmark {
    font-weight: 700;
    font-size: 60px;
    line-height: 1;
    letter-spacing: -1px;
  }
  .front-brand {
    position: absolute;
    left: 30px;
    top: 80px;
    color: var(--brand-blue);
  }

  .front-band-rule {
    position: absolute;
    left: 0; right: 0;
    top: 162px;
    height: 3px;
    background: var(--brand-blue);
  }
  .front-band {
    position: absolute;
    left: 0; right: 0;
    top: 168px;
    bottom: 0;
    background: var(--brand-blue);
    color: var(--paper);
  }
  .holder {
    position: absolute;
    left: 43px;
    top: 48px;
  }
  .holder-name { font-weight: 700; font-size: 17px; line-height: 1.1; }
  .holder-title { font-size: 13px; margin-top: 5px; }

  .divider {
    position: absolute;
    top: 28px;
    width: 1px;
    height: 74px;
    background: var(--paper);
  }
  .divider-contact { left: 172px; }
  .divider-address { left: 335px; }

  .contact-list {
    position: absolute;
    left: 184px;
    top: 26px;
    list-style: none;
    font-size: 13.5px;
    line-height: 18px;
  }
  .contact-list li { display: flex; align-items: center; gap: 7px; }
  .contact-list svg { width: 10px; height: 10px; fill: var(--paper); flex: none; }

  .address {
    position: absolute;
    left: 347px;
    top: 26px;
    font-size: 13.5px;
    line-height: 18px;
    font-style: normal;
  }

  .back-brand {
    position: absolute;
    left: 0; right: 0;
    top: 108px;
    text-align: center;
    color: var(--paper);
  }
  .back-brand .wordmark { font-size: 56px; }
  .back-url {
    margin-top: 22px;
    font-size: 12px;
    letter-spacing: 2.4px;
  }
</style>
</head>
<body>
  <section class="card card-front" aria-label="Card front">
    <div class="front-brand">
      <div class="wordmark">HALVERN</div>
    </div>
    <div class="front-band-rule"></div>
    <div class="front-band">
      <div class="holder">
        <div class="holder-name">YOUR NAME</div>
        <div class="holder-title">Title</div>
      </div>
      <div class="divider divider-contact"></div>
      <ul class="contact-list">
        <li><svg viewBox="0 0 10 10" aria-hidden="true"><path d="M2 0.5 L3.6 2.8 L2.7 3.8 Q3.6 5.9 6.2 7.3 L7.2 6.4 L9.5 8 L8.3 9.5 Q3.5 9 0.5 1.7 Z"/></svg>0945127836</li>
        <li><svg viewBox="0 0 10 10" aria-hidden="true"><path d="M0.5 3 Q5 0.5 9.5 3 L9.5 4.5 L7 4.5 L7 3.5 L3 3.5 L3 4.5 L0.5 4.5 Z M1.5 5.5 L8.5 5.5 L8.5 9.5 L1.5 9.5 Z"/></svg>0945127836</li>
        <li><svg viewBox="0 0 10 10" aria-hidden="true"><path d="M0.5 2 L9.5 2 L5 5.5 Z M0.5 3.2 L5 6.7 L9.5 3.2 L9.5 8.5 L0.5 8.5 Z"/></svg>info@halvern.com</li>
        <li><svg viewBox="0 0 10 10" aria-hidden="true"><path d="M5 0.5 A4.5 4.5 0 1 0 5.01 0.5 Z M5 1.5 Q3.3 3 3.3 5 Q3.3 7 5 8.5 Q6.7 7 6.7 5 Q6.7 3 5 1.5 Z M1.5 4.5 L8.5 4.5 L8.5 5.5 L1.5 5.5 Z" fill-rule="evenodd"/></svg>www.halvern.com</li>
      </ul>
      <div class="divider divider-address"></div>
      <address class="address">
        627 West Dorrance Blvd<br>
        Suite 308<br>
        Anaheim, CA 92718
      </address>
    </div>
  </section>

  <section class="card card-back" aria-label="Card back">
    <div class="back-brand">
      <div class="wordmark">HALVERN</div>
      <div class="back-url">www.halvern.com</div>
    </div>
  </section>
</body>
</html>
```